Kelvo bottle Label (Yoghurt drink)

Label for a 300 ml yoghurt drink bottle in 3 flavours.

General description:
• This is to design a sleeve shrink label for a Yoghurt Drink bottle in three flavours, Classic, Strawberry and Blueberry.
• Attached 3 photos: The one with KELVO brand in the current design we want to replace using the same bottle.
• Graphically, the design is to be similar to the examples provided for drumelo and fizzcrate.
• Use font and barcode size to be readable and legal.
• Minimize the use of the upper third of the bottle as it will be distorted when the label shrinks to the bottle.
• Professional and experienced designers only are welcome, please do not waste your time otherwise.

Bottle dimensions:
• Base across: 61 mm
• Height: 145 mm (approximate)

Graphical description:
• White colour with bands at the top and bottom similar to the one in “drumelo” example provided (not necessarily identical, feel free to be creative.
• The upper and lower bands to be: Green for “classic”, Pink or red for strawberry and purple for blueberry flavour.
• On the front: the brand name “Kelvo” and description “Yoghurt Drink” to be graphically attractive.
• On the front: two or more pieces of strawberry or blueberry for each flavour placed nicely with the option to include “yoghurt splash” or any suitable affects you deem suitable.
• For the Classic flavour, use the words (Classic, Lassi, Ayran) in the same location for the berries done in a graphically suitable manner.
• Colour temperature for the three flavours to be similar.

Information and objects on the label:
Front:
• The word “Kelvo” (brand name)
• “Yoghurt drink” (Product description)
• “300 ml” (size)
• Picture of Strawberries for strawberry flavour.
• Picture of Blueberries for blueberry flavour.
• The words (Classic, Lassi, Ayran) in the place used for the strawberries in the flavoured type, distributed to look graphically suitable for the overall design.

Back:
• Ingredient: Milk/milk solids, culture, salt, water, sugar, colour, flavour. (this is to be finalized later)
• Nutrition information table: (to be provided later).
• Barcode (to be provided later)
• Product of Australia
• Morel Tunsley Pty Ltd, 5/14 Ferrit St, Malaga, WA 6090
• info@kelvo-example.com.au 0491 000 372
• Keep under 5⁰ C
• Best before date printed on the bottle
• Shake well (to be located on the side at the top)
• Recycle icon.

Health benefits: (to be located suitably, possibly on the side with vertical orientation)
• Rich in probiotic bacteria and vitamins.
• Improves digestion and bowel motion.
• Supports weight control and fat loss.

Target Market(s)

General consumers

Industry/Entity Type

Grocery Store

Font styles to use
Sans Serif

Colors
abd037
b768aa
f04a50

Requirements
Must have
• The details in the project description
• The design must be simple and neat.
• Please use the shape of the current bottle "Kelvo" as in the attached photo.
Should not have
• Busy, cluttered, or empty and incomplete designs.

```html
<!DOCTYPE html>
<html lang="en">
<head>
<meta charset="utf-8">
<title>Kelvo Yoghurt Drink – Strawberry Label</title>
<link rel="stylesheet" href="https://fonts.googleapis.com/css2?family=PT+Sans+Narrow:wght@400;700&family=PT+Sans:wght@400;700&family=Pinyon+Script&display=swap">
<style>
  :root {
    --brand-rose: #d85a68;
    --stripe-red: #e8474f;
    --band-red: #cc3a42;
    --band-shadow: #b9b9bb;
    --text-grey: #a4a6a9;
    --flavour-red: #c8242d;
    --cap-white: #f4f4f2;
    --cap-line: #dcdcd8;
    --neck-cream: #efedd8;
    --bottle-edge: #e6e6e6;
    --berry-red: #d8323a;
    --page: #ffffff;
  }
  html, body { margin: 0; padding: 0; overflow: hidden; background: var(--page); }
  .canvas { width: 1200px; height: 829px; position: relative; overflow: hidden; background: var(--page); }
  .canvas svg { display: block; }
  .cap { fill: var(--cap-white); stroke: var(--cap-line); stroke-width: 1.5; }
  .cap-ring { fill: none; stroke: var(--cap-line); stroke-width: 2; }
  .neck { fill: var(--neck-cream); }
  .body { fill: var(--page); stroke: var(--bottle-edge); stroke-width: 1.5; }
  .stripe { fill: var(--stripe-red); }
  .band { fill: var(--band-red); }
  .band-edge { fill: var(--band-shadow); }
  .brand { font-family: "PT Sans Narrow", "Arial Narrow", sans-serif; font-weight: 700; fill: var(--brand-rose); }
  .descriptor { font-family: "PT Sans", Arial, sans-serif; fill: var(--text-grey); letter-spacing: 1px; }
  .descriptor .bold { font-weight: 700; }
  .flavour { font-family: "PT Sans Narrow", "Arial Narrow", sans-serif; fill: var(--flavour-red); }
  .flavour-sub { font-family: "PT Sans", Arial, sans-serif; fill: var(--text-grey); }
  .flavour-script { font-family: "Pinyon Script", cursive; fill: var(--flavour-red); }
  .divider { stroke: var(--text-grey); stroke-width: 1.5; }
  .band-text { font-family: "PT Sans", Arial, sans-serif; fill: #ffffff; font-size: 13px; }
  .volume-tag { font-family: "PT Sans", Arial, sans-serif; fill: #ffffff; font-size: 14px; }
  .berry-art { fill: var(--berry-red); }
</style>
</head>
<body>
<div class="canvas">
<svg width="1200" height="829" viewBox="0 0 1200 829" xmlns="http://www.w3.org/2000/svg">
  <defs>
    <path id="bottle-body" d="M-86,208 C-112,262 -126,330 -126,420 L-128,760 C-128,800 -110,816 -80,816 L80,816 C110,816 128,800 128,760 L126,420 C126,330 112,262 86,208 Z"/>
    <g id="bottle-top">
      <path class="neck" d="M-88,160 L88,160 L92,205 C60,218 -60,218 -92,205 Z"/>
      <rect class="cap" x="-90" y="62" width="180" height="100" rx="8"/>
      <line class="cap-ring" x1="-90" y1="132" x2="90" y2="132"/>
      <line class="cap-ring" x1="-90" y1="146" x2="90" y2="146"/>
    </g>
    <path id="band-curve-left" d="M-118,742 C-60,780 40,798 118,760"/>
    <path id="band-curve-right" d="M-118,746 C-60,784 40,802 118,764"/>
  </defs>

  <!-- Front A: stripe + brand -->
  <g class="bottle bottle--stripe" transform="translate(230,0)">
    <use href="#bottle-body" class="body"/>
    <use href="#bottle-top"/>
    <rect class="stripe" x="-12" y="228" width="18" height="274"/>
    <text class="brand" x="0" y="590" text-anchor="middle" font-size="98" textLength="226" lengthAdjust="spacingAndGlyphs">KELVO</text>
    <text class="descriptor" x="0" y="630" text-anchor="middle" font-size="22">YOGHURT <tspan class="bold">DRINK</tspan></text>
    <path class="band-edge" d="M-127,692 C-70,742 40,760 127,712 L127,722 C40,770 -70,752 -127,702 Z"/>
    <path class="band" d="M-127,700 C-70,750 40,768 127,720 L128,760 C128,800 110,816 80,816 L-80,816 C-110,816 -128,800 -128,760 Z"/>
    <text class="flavour" x="-112" y="664" font-size="22" textLength="80" lengthAdjust="spacingAndGlyphs" transform="rotate(6 -112 664)">Strawberry</text>
    <text class="flavour-sub" x="-70" y="684" font-size="13" transform="rotate(6 -70 684)">Flavour</text>
    <line class="divider" x1="-12" y1="652" x2="-12" y2="704"/>
    <ellipse class="berry-art" cx="56" cy="680" rx="42" ry="26" role="img" aria-label="Two ripe strawberries"/>
    <text class="band-text"><textPath href="#band-curve-left" startOffset="2%">100% Natural Ingredients</textPath></text>
    <text class="band-text" x="88" y="770" font-size="13" transform="rotate(-22 88 770)">300ml.</text>
  </g>

  <!-- Front B: berries + stacked type -->
  <g class="bottle bottle--berries" transform="translate(620,0)">
    <use href="#bottle-body" class="body"/>
    <use href="#bottle-top"/>
    <rect class="stripe" x="-12" y="228" width="18" height="240"/>
    <ellipse class="berry-art" cx="-2" cy="520" rx="94" ry="50" role="img" aria-label="Two large ripe strawberries"/>
    <text class="brand" x="0" y="656" text-anchor="middle" font-size="112" textLength="240" lengthAdjust="spacingAndGlyphs">KELVO</text>
    <text class="descriptor" x="0" y="690" text-anchor="middle" font-size="30">YOGHURT</text>
    <text class="descriptor" x="0" y="726" text-anchor="middle" font-size="40"><tspan class="bold">DRINK</tspan></text>
    <text class="flavour-script" x="0" y="758" text-anchor="middle" font-size="28">Strawberry</text>
    <rect class="stripe" x="-13" y="766" width="26" height="50"/>
    <text class="volume-tag" x="0" y="782" text-anchor="middle">300</text>
    <text class="volume-tag" x="0" y="797" text-anchor="middle">ml.</text>
  </g>

  <!-- Front C: vertical brand -->
  <g class="bottle bottle--vertical" transform="translate(980,0)">
    <use href="#bottle-body" class="body"/>
    <use href="#bottle-top"/>
    <path class="band-edge" d="M-98,248 C-40,262 40,262 100,272 L98,282 C40,274 -40,274 -100,258 Z"/>
    <path class="band" d="M-94,220 C-40,234 40,236 96,240 C102,250 104,262 100,270 C40,262 -40,262 -100,248 C-99,238 -97,228 -94,220 Z"/>
    <text class="brand" x="0" y="0" text-anchor="middle" font-size="120" transform="translate(42,444) rotate(-90)" textLength="290" lengthAdjust="spacingAndGlyphs">KELVO</text>
    <text class="descriptor" x="0" y="632" text-anchor="middle" font-size="22">YOGHURT <tspan class="bold">DRINK</tspan></text>
    <path class="band-edge" d="M-127,700 C-70,748 40,764 127,716 L127,726 C40,774 -70,758 -127,710 Z"/>
    <path class="band" d="M-127,708 C-70,756 40,772 127,724 L128,760 C128,800 110,816 80,816 L-80,816 C-110,816 -128,800 -128,760 Z"/>
    <text class="flavour" x="-106" y="672" font-size="22" textLength="80" lengthAdjust="spacingAndGlyphs" transform="rotate(6 -106 672)">Strawberry</text>
    <text class="flavour-sub" x="-64" y="692" font-size="13" transform="rotate(6 -64 692)">Flavour</text>
    <line class="divider" x1="-4" y1="660" x2="-4" y2="712"/>
    <ellipse class="berry-art" cx="60" cy="690" rx="42" ry="26" role="img" aria-label="Two ripe strawberries"/>
    <text class="band-text"><textPath href="#band-curve-right" startOffset="2%">100% Natural Ingredients</textPath></text>
    <text class="band-text" x="88" y="774" font-size="13" transform="rotate(-22 88 774)">300ml.</text>
  </g>
</svg>
</div>
</body>
</html>
```